interior designer/stylist looking for a letter press business card to reflect the stylish work

Hello Designers,
I need a business card design for an company called Mosaic Interior Design. I'm aiming at the high end residential and private client market in London providing sleek simple interiors. I'd like my business card to be pinterest worthy and expensive looking, i want people to pin it and for it to have a sought after look, and want prospective customers to hire me as their interior designer as my card is so beautiful.
I love letter press design. I also like the use of colour/foil on the edge.
Colour combos & general things I like -
Black and White
Navy Blue and Gold
Neutral colours (muted palette of greys whites navys beiges)
White Marble & brass
Vorelle (fashion designer)
....also open to other suggestions....
Please dont take the pink in the attached photos too literally. i'd like the card to look more masculine than feminine.
I'd like Mosaic on one side in one font, with interior design underneath so one word will make the statement....... unless anyone has any other ideas, open to suggestions.
I'd like a really simple font and for the whole card to look very graphic.
my details -
Petra Wendlecombe
Interior Designer & Stylist
email petra@mosaicinteriordesign.co.uk
phone +447311584209
website wwww.mosaicinteriordesign.co.uk
GO GO GO!! EXCITED TO SEE THE OUTCOME!!
x P
Target Market(s)
High End Residential and private clients
Industry/Entity Type
Business
Contact Information for Business Card
Mosaic Interior Design & Styling
Petra Wendlecombe
phone +447311584209

```html
<!DOCTYPE html>
<html lang="en">
<head>
<meta charset="utf-8">
<title>Mosaic Interior Design &amp; Styling — Business Card</title>
<link rel="stylesheet" href="https://fonts.googleapis.com/css2?family=Josefin+Sans:wght@300;400&display=swap">
<style>
  :root {
    --backdrop: #5e5e5f;
    --card-stock: #f7f6f2;
    --foil-gold: #c9a227;
    --foil-edge: #d8bb5a;
    --foil-ink: #b8922a;
  }
  * { box-sizing: border-box; margin: 0; padding: 0; }
  html, body {
    width: 872px;
    height: 1200px;
    overflow: hidden;
    background: var(--backdrop);
  }
  .sheet {
    width: 872px;
    height: 1200px;
    display: flex;
    flex-direction: column;
    align-items: center;
    justify-content: center;
    gap: 140px;
  }
  .card {
    position: relative;
    width: 630px;
    height: 360px;
    background: var(--card-stock);
    border: 4px solid var(--foil-edge);
    box-shadow: 0 18px 40px rgba(0, 0, 0, 0.35);
    font-family: "Josefin Sans", sans-serif;
    color: var(--foil-gold);
  }
  .card-front .brand {
    position: absolute;
    left: 300px;
    top: 132px;
  }
  .brand-name {
    font-weight: 300;
    font-size: 64px;
    letter-spacing: 6px;
    line-height: 1;
  }
  .brand-tagline {
    margin-top: 8px;
    font-weight: 400;
    font-size: 12px;
    letter-spacing: 3.2px;
    text-transform: uppercase;
    color: var(--foil-ink);
  }
  .card-back .contact {
    position: absolute;
    left: 300px;
    top: 118px;
    font-weight: 300;
    color: var(--foil-ink);
  }
  .contact-name {
    font-size: 20px;
    letter-spacing: 1.5px;
    font-weight: 400;
    color: var(--foil-gold);
  }
  .contact-role {
    margin-top: 6px;
    font-size: 13px;
    letter-spacing: 1.2px;
  }
  .contact-lines {
    margin-top: 26px;
    list-style: none;
    font-size: 12px;
    letter-spacing: 0.8px;
    line-height: 1.9;
  }
</style>
</head>
<body>
  <main class="sheet">
    <section class="card card-front" aria-label="Card front">
      <div class="brand">
        <div class="brand-name">MOSAIC</div>
        <div class="brand-tagline">Interior Design &amp; Styling</div>
      </div>
    </section>

    <section class="card card-back" aria-label="Card back">
      <div class="contact">
        <div class="contact-name">Petra Wendlecombe</div>
        <div class="contact-role">Interior Designer &amp; Stylist</div>
        <ul class="contact-lines">
          <li>+447311584209</li>
          <li>petra@mosaicinteriordesign.co.uk</li>
          <li>wwww.mosaicinteriordesign.co.uk</li>
        </ul>
      </div>
    </section>
  </main>
</body>
</html>
```